IT Company requires new Business Card design.

Over the years we have had a few different business card designs. We are now due for new cards across the board for all staff. We felt this would be a good time to start fresh with a new design. Our traditional card simply had our details on the front, and a list of services on the back. We don't particularly need the list of services, we have had cards where the only thing on the rear of the card was our logo.
Feel free to be creative, we would like our tag line "Complete IT Management" to appear at some point, doesn't necessarily have to be with the logo.
I have attached samples and drafts of various previous cards we have used over the years.

```html
<!DOCTYPE html>
<html lang="en">
<head>
<meta charset="utf-8">
<title>Ridgeway Networks – Business Card</title>
<link href="https://fonts.googleapis.com/css2?family=Open+Sans:wght@400;700&display=swap" rel="stylesheet">
<style>
  :root {
    --stage: #e3e3e8;
    --card: #ffffff;
    --slate: #607482;
    --charcoal: #4a4a4c;
    --ink: #4e4e50;
    --white: #ffffff;
  }
  * { margin: 0; padding: 0; box-sizing: border-box; }
  html, body {
    width: 1200px; height: 987px; overflow: hidden;
    background: var(--stage);
    font-family: "Open Sans", Arial, sans-serif;
  }
  .stage { position: relative; width: 1200px; height: 987px; }
  .card {
    position: absolute; left: 240px;
    width: 720px; height: 412px;
    background: var(--card);
    border-radius: 30px;
    overflow: hidden;
    box-shadow: 0 6px 18px rgba(0,0,0,0.12);
  }
  .card--back { top: 48px; }
  .card--front { top: 520px; }

  /* back */
  .back-brand {
    position: absolute; left: 0; right: 0; top: 120px;
    display: flex; align-items: center; justify-content: center; gap: 18px;
    color: var(--slate); font-weight: 700;
  }
  .brand-square { width: 56px; height: 56px; background: var(--slate); }
  .back-brand .brand-name { font-size: 48px; line-height: 1; letter-spacing: 1px; }
  .back-web {
    position: absolute; left: 0; right: 0; top: 300px; text-align: center;
    color: var(--ink); font-size: 20px; letter-spacing: 2px;
  }

  /* front */
  .accent-bar { position: absolute; left: 0; top: 32px; width: 14px; height: 46px; background: var(--slate); }
  .person { position: absolute; left: 40px; top: 28px; }
  .person-name { color: var(--slate); font-weight: 700; font-size: 22px; line-height: 1.2; }
  .person-role { color: var(--ink); font-size: 16px; line-height: 1.3; }
  .address { position: absolute; left: 40px; top: 100px; color: var(--ink); font-size: 16px; line-height: 1.35; }
  .contacts { position: absolute; left: 40px; top: 160px; list-style: none; color: var(--ink); font-size: 15px; line-height: 1.55; }
  .contacts li { display: flex; align-items: center; gap: 8px; }
  .contacts svg { width: 14px; height: 14px; fill: var(--slate); flex: none; }
  .footer-bands { position: absolute; left: 0; top: 0; width: 720px; height: 412px; }
  .tagline { position: absolute; left: 30px; top: 322px; color: var(--white); font-size: 16px; }
  .front-brand {
    position: absolute; left: 420px; top: 170px;
    display: flex; align-items: center; gap: 16px;
    color: var(--slate); font-weight: 700;
  }
  .front-brand .brand-square { width: 46px; height: 46px; }
  .front-brand .brand-name { font-size: 34px; line-height: 1.05; }
</style>
</head>
<body>
<main class="stage">

  <section class="card card--back" aria-label="Card back">
    <div class="back-brand">
      <span class="brand-square"></span>
      <span class="brand-name">RIDGEWAY NETWORKS</span>
    </div>
    <p class="back-web">www.ridgewaynetworks.com.au</p>
  </section>

  <section class="card card--front" aria-label="Card front">
    <svg class="footer-bands" viewBox="0 0 720 412" aria-hidden="true">
      <path d="M0 314 H360 C392 314 398 344 430 344 H720 V412 H0 Z" fill="var(--slate)"/>
      <path d="M0 352 H350 C384 352 394 374 428 374 H720 V412 H0 Z" fill="var(--charcoal)"/>
    </svg>
    <span class="accent-bar"></span>
    <div class="person">
      <p class="person-name">Daniel Hart</p>
      <p class="person-role">Operation Manager</p>
    </div>
    <p class="address">Unit 7 22 Harbour Road<br>Kelmscott WA 6111</p>
    <ul class="contacts">
      <li><svg viewBox="0 0 16 16"><circle cx="8" cy="8" r="7.5"/></svg>08 5550 1842</li>
      <li><svg viewBox="0 0 16 16"><rect x="4" y="1" width="8" height="14" rx="1.5"/></svg>0400 555 219</li>
      <li><svg viewBox="0 0 16 16"><rect x="1" y="6" width="14" height="8" rx="1"/><rect x="4" y="1" width="8" height="5"/></svg>08 5550 1842</li>
      <li><svg viewBox="0 0 16 16"><path d="M1 4 H15 V13 H1 Z M1 4 L8 9 L15 4"/></svg>daniel@ridgewaynetworks.com.au</li>
      <li><svg viewBox="0 0 16 16"><circle cx="8" cy="8" r="7"/></svg>www.ridgewaynetworks.com.au</li>
    </ul>
    <p class="tagline">Complete IT Management</p>
    <div class="front-brand">
      <span class="brand-square"></span>
      <span class="brand-name">RIDGEWAY<br>NETWORKS</span>
    </div>
  </section>

</main>
</body>
</html>
```